Business card for event manager / organizer "waiter service"

Draft of a new valuable business card for my company.
Events, personnel service providers, festivals

```html
<!DOCTYPE html>
<html lang="de">
<head>
<meta charset="utf-8">
<title>Anker Servicecrew – Visitenkarte</title>
<link rel="stylesheet" href="https://fonts.googleapis.com/css2?family=Open+Sans:wght@300;600;700;800&display=swap">
<style>
  :root {
    --bg: #6d6e72;
    --card: #0b0b0d;
    --gold: #b8996b;
    --gold-text: #c2a06d;
    --muted-gold: #8a7a64;
    --white: #ffffff;
    --photo-dark: #3a3a3e;
    --photo-light: #8d8d92;
  }
  * { margin: 0; padding: 0; box-sizing: border-box; }
  html, body { width: 1200px; height: 1200px; overflow: hidden; background: var(--bg); font-family: "Open Sans", sans-serif; }
  .card { position: absolute; background: var(--card); border-radius: 30px; overflow: hidden; }
  .card-front { left: 222px; top: 104px; width: 756px; height: 431px; }
  .card-back { left: 215px; top: 655px; width: 760px; height: 428px; }

  .brand { position: absolute; display: flex; align-items: center; }
  .brand-mark { background: var(--gold); flex: none; }
  .brand-name { color: var(--white); font-weight: 800; text-transform: uppercase; line-height: 1.05; }
  .tagline { position: absolute; color: var(--gold); font-weight: 300; white-space: nowrap; }

  .card-front .brand { left: 230px; top: 178px; gap: 16px; }
  .card-front .brand-mark { width: 64px; height: 64px; }
  .card-front .brand-name { font-size: 30px; }
  .card-front .tagline { left: 300px; top: 250px; font-size: 11px; }
  .front-url { position: absolute; left: 0; right: 0; top: 393px; text-align: center; color: var(--muted-gold); font-weight: 700; font-size: 15px; letter-spacing: 4px; }

  .card-back .brand { left: 37px; top: 40px; gap: 10px; }
  .card-back .brand-mark { width: 40px; height: 40px; }
  .card-back .brand-name { font-size: 17px; }
  .card-back .tagline { left: 84px; top: 92px; font-size: 7px; }

  .name-band { position: absolute; left: 0; right: 0; top: 144px; height: 61px; background: var(--gold); }
  .person-name { position: absolute; left: 37px; top: 154px; color: var(--white); font-weight: 700; font-size: 22px; letter-spacing: 5px; }
  .person-role { position: absolute; left: 37px; top: 182px; color: var(--white); font-weight: 700; font-size: 14px; letter-spacing: 3px; }

  .portrait { position: absolute; left: 495px; top: 84px; width: 180px; height: 180px; border-radius: 50%; border: 3px solid var(--gold);
    background: radial-gradient(circle at 55% 35%, var(--photo-light), var(--photo-dark) 75%); }

  .contact-list { position: absolute; left: 38px; top: 231px; list-style: none; }
  .contact-item { display: flex; align-items: center; height: 35px; }
  .contact-item svg { width: 29px; height: 29px; flex: none; }
  .contact-text { margin-left: 24px; color: var(--gold-text); font-weight: 700; font-size: 12.5px; line-height: 1.25; text-transform: uppercase; }
</style>
</head>
<body>

<section class="card card-front">
  <div class="brand">
    <span class="brand-mark"></span>
    <span class="brand-name">Anker<br>Servicecrew</span>
  </div>
  <p class="tagline">..weil jedes Fest gute Gastgeber verdient!</p>
  <p class="front-url">WWW.ANKER-SERVICECREW.DE</p>
</section>

<section class="card card-back">
  <div class="brand">
    <span class="brand-mark"></span>
    <span class="brand-name">Anker<br>Servicecrew</span>
  </div>
  <p class="tagline">..weil jedes Fest gute Gastgeber verdient!</p>

  <div class="name-band"></div>
  <p class="person-name">JONAS BRETTNER</p>
  <p class="person-role">INHABER</p>
  <div class="portrait" role="img" aria-label="Porträtfoto des Inhabers"></div>

  <ul class="contact-list">
    <li class="contact-item">
      <svg viewBox="0 0 30 30"><circle cx="15" cy="15" r="13.5" fill="none" stroke="#b8996b" stroke-width="1.5"/><path d="M10 8.5l3 0 1.2 3.6-1.8 1.4c.9 2 2.4 3.5 4.3 4.4l1.4-1.8 3.6 1.2 0 3c0 .8-.7 1.3-1.5 1.3C13.9 21 9 16.1 8.7 10c0-.8.5-1.5 1.3-1.5z" fill="none" stroke="#b8996b" stroke-width="1.4" stroke-linejoin="round"/></svg>
      <span class="contact-text">02361 555 12 34<br>0170 555 98 76</span>
    </li>
    <li class="contact-item">
      <svg viewBox="0 0 30 30"><circle cx="15" cy="15" r="13.5" fill="none" stroke="#b8996b" stroke-width="1.5"/><g fill="none" stroke="#b8996b" stroke-width="1.2"><circle cx="15" cy="15" r="8"/><ellipse cx="15" cy="15" rx="3.5" ry="8"/><path d="M7 15h16M8.2 11h13.6M8.2 19h13.6"/></g></svg>
      <span class="contact-text">WWW.ANKER-SERVICECREW.DE</span>
    </li>
    <li class="contact-item">
      <svg viewBox="0 0 30 30"><circle cx="15" cy="15" r="13.5" fill="none" stroke="#b8996b" stroke-width="1.5"/><path d="M8 13l7-5 7 5v8H8z M8 13l7 5 7-5" fill="none" stroke="#b8996b" stroke-width="1.3" stroke-linejoin="round"/></svg>
      <span class="contact-text">INFO@ANKER-SERVICECREW.DE</span>
    </li>
    <li class="contact-item">
      <svg viewBox="0 0 30 30"><circle cx="15" cy="15" r="13.5" fill="none" stroke="#b8996b" stroke-width="1.5"/><path d="M7.5 15.5L15 9l7.5 6.5h-2v6h-4v-4h-3v4h-4v-6z" fill="#b8996b"/></svg>
      <span class="contact-text">LINDENWEG 12, 45100<br>MUSTERSTADT</span>
    </li>
    <li class="contact-item">
      <svg viewBox="0 0 30 30"><circle cx="15" cy="15" r="13.5" fill="none" stroke="#b8996b" stroke-width="1.5"/></svg>
      <span class="contact-text">WWW.SOCIAL.EXAMPLE/ANKERSERVICECREW</span>
    </li>
  </ul>
</section>

</body>
</html>
```